International sourcing and trading company needs website design on Squarespace

We are international sourcing and trading company based in Brisbane ,Australia. We help our clients to source any products they need to economically produce overseas and we manage the whole production process for them. We want our visual identity to show that we are professional, dynamic, efficient and are able to source any product around the world. Our website will be simply information and advertising website , no ecommerce or any transactions. Please see attached our company logo. We would like our website to have the following sections/pages:

1.Main banner with a simple slogan/sentence to introduce what we do: Let us handle the overseas sourcing and production for you.

2. Post-Covid sourcing and producing management: introducing our competence on managing sourcing and overseas production under the travel restriction and the growing tension on global trading. We will supply the exact wording later on;

3. About us: We are a professional team with mature global sourcing and trading experience. We have branch office in Hong Kong and local resources around all areas in China , India and other Asian countries. Our working flow is: received inquiry->start sourcing->(in 1 week time)give price and delivery date on inquired products or further information->(if needed)arrange samples for clients->(if samples and orders are confirmed)deliver Pre-production sample-> kick-off production->arrange inspection through the whole production-> (if need) arrange shipment to client. We would like to show the work flow in a personalized way , eg. personalize icons etc.;

4. What kind of product we can source and produce: our business is sourcing and managing manufacture overseas for our clients, product categories mainly, but not just, are clothing, shoes , bags, clothing accessories, makeup accessories, festival or promotional gifts etc. all kind of daily use products . We basically are able to source and manage production of every kind of products with no limits. We would like this page to be particularly personalized in a way to give impression to whom browse our website feel free to send inquiry of any kind of production to us and they can trust us that we will do our job professionally and dynamically. We are thinking of using some icons of daily use products to show our sourcing category , it's just our though so please feel free to propose any other ides that you think is more suitable from the point of view of professional designer.

5. Start an enquiry: here we need to land on a questionary page to let who would like to make en enquiry leave the main information , including:
-Name & Sir name:
-Company name:
-Contact email:
-Phone numer:
-Enquired product:
-Upload image:
-Preferred or previous production country:
-Preferred price: FOB, CIF, DDP
-If CIF or DDP where the arrival port/airport will be:
-Preferred delivery time:
-Preferred transportation: by air, by sea, by train
- Other specific requires:

6: Contact us: We will supply contact info later on

Above are our thoughts but please feel free to propose any other ideas that you think should be more suitable for us. We trust your expertise and professional opinions.

Wholesalers and retailers who need to produce their products overseas (mainly in China and other countries in Asia)

• We think it will be nice to show information in simple and comprehensive icons instead of piles of words. We will want our website neat, easy to understand what we do and professional. However this is just our thought so please feel free to propose any other ideas that you think is more suitable from the point of view of professional designer.

```html
<!DOCTYPE html>
<html lang="en">
<head>
<meta charset="utf-8">
<title>CargoBloom – Global sourcing and trading</title>
<link href="https://fonts.googleapis.com/css2?family=Righteous&family=Varela+Round&family=Quicksand:wght@500;700&display=swap" rel="stylesheet">
<style>
:root{
  --orange:#f5a33b;
  --teal:#4fb8c9;
  --dark:#3a3a3a;
  --ink:#2e2e2e;
  --grey-bg:#f3f3f3;
  --text:#444;
  --white:#fff;
}
*{box-sizing:border-box;margin:0;padding:0}
html,body{width:1200px;height:3827px;overflow:hidden}
body{position:relative;background:var(--white);font-family:"Varela Round",sans-serif;color:var(--text)}
.abs{position:absolute}
.notice{left:0;top:0;width:1200px;height:58px;background:var(--orange);color:var(--white);font-family:"Quicksand",sans-serif;font-size:12px;line-height:18px;text-align:center;padding:10px 260px 0}
.notice strong{font-size:15px;font-weight:500}
.notice-close{right:20px;top:17px;width:24px;height:24px;border-radius:50%;background:var(--white);color:var(--orange);font-size:18px;line-height:24px;text-align:center;font-weight:700}
.nav{left:0;top:58px;width:1200px;height:89px;background:var(--white)}
.brand{left:172px;top:80px;display:flex;align-items:center;gap:12px}
.brand-dot{width:44px;height:44px;border-radius:50%;background:var(--orange)}
.brand-name{font-family:"Quicksand",sans-serif;font-weight:700;font-size:30px;color:var(--orange);line-height:1}
.brand-tag{font-family:"Quicksand",sans-serif;font-weight:700;font-size:13px;color:var(--orange)}
.menu{right:172px;top:104px;display:flex;gap:16px;font-size:14px;color:var(--ink)}
.menu .active{color:var(--orange);text-decoration:underline}
.hero{left:0;top:147px;width:1200px;height:551px;overflow:hidden}
.hero-photo{position:absolute;inset:0;background:linear-gradient(180deg,#9aa8b3 0%,#6f8594 30%,#3f5d6f 60%,#2c4a5a 100%)}
.hero-photo::after{content:"";position:absolute;left:560px;top:80px;width:640px;height:420px;background:linear-gradient(120deg,#b8553f,#3c6aa8 40%,#d99a3f 70%,#3d5d8a);opacity:.55;transform:skewX(-20deg)}
.hero-title{left:172px;top:282px;font-family:"Varela Round",sans-serif;font-size:92px;color:var(--white);letter-spacing:-2px;font-weight:700;text-shadow:0 2px 6px rgba(0,0,0,.3)}
.hero-sub{left:172px;top:402px;font-family:"Quicksand",sans-serif;font-style:italic;font-size:30px;line-height:42px;color:var(--white);text-shadow:0 2px 4px rgba(0,0,0,.4)}
.hero-wave{left:0;top:598px}
.sec-head{display:flex;align-items:center;gap:14px;font-family:"Righteous",sans-serif;font-size:50px;line-height:1;color:var(--ink)}
.sec-head .hl{color:var(--orange)}
.sec-mark{width:58px;height:58px;border-radius:50%;background:var(--teal)}
.about-head{left:172px;top:806px}
.about-text{left:172px;top:892px;width:456px;font-size:17px;line-height:31px;text-align:justify}
.btn{display:block;text-align:center;font-family:"Righteous",sans-serif;color:var(--white);border-radius:30px}
.btn-more{left:172px;top:1043px;width:141px;height:56px;line-height:56px;background:var(--teal);font-size:19px}
.about-visual{left:700px;top:810px;width:330px;height:300px;border-radius:50%;background:radial-gradient(circle at 40% 40%,#bfe6ec,var(--teal));opacity:.9}
.flow-bg{left:0;top:1180px}
.flow-head{left:0;top:1318px;width:1200px;justify-content:center}
.step{width:192px;height:152px;background:var(--white);box-shadow:0 2px 6px rgba(0,0,0,.15);text-align:center;font-size:16px;line-height:22px;color:var(--ink);padding:0 6px}
.step svg{display:block;margin:24px auto 12px}
.step .lbl{height:50px;display:flex;align-items:center;justify-content:center}
.flow-end{left:832px;top:1850px;width:180px;height:150px;border-radius:50%;background:radial-gradient(circle at 40% 40%,#bfe6ec,var(--teal))}
.cat-bg{left:0;top:2090px}
.cat-head{left:0;top:2228px;width:1200px;justify-content:center}
.cat{width:222px;height:222px;border-radius:50%;border:3px solid var(--white);overflow:hidden;box-shadow:0 2px 8px rgba(0,0,0,.3)}
.cat-fill{position:absolute;inset:0}
.cat-label{position:absolute;left:0;bottom:0;width:100%;height:70px;line-height:56px;text-align:center;font-family:"Righteous",sans-serif;font-size:21px;color:var(--white)}
.chev{top:2455px}
.enq-bg{left:0;top:2900px;width:1200px;height:520px;background:linear-gradient(180deg,rgba(255,255,255,1) 0%,rgba(255,255,255,.6) 25%,rgba(120,150,170,.55) 70%,rgba(70,110,140,.7) 100%)}
.enq-head{left:0;top:2860px;width:1200px;justify-content:center}
.field{height:51px;border:1.5px solid #555;border-radius:26px;background:var(--white);font-size:15px;color:var(--ink);padding:15px 16px}
.msg{left:172px;top:3052px;width:856px;height:141px;border-radius:30px;padding:16px 22px}
.btn-submit{left:524px;top:3233px;width:150px;height:49px;line-height:49px;background:var(--orange);font-size:17px}
.foot-wave{left:0;top:3350px}
.footer{left:0;top:3420px;width:1200px;height:407px;background:var(--dark)}
.foot-brand{left:172px;top:3530px;text-align:center;width:260px}
.foot-brand .brand-dot{width:60px;height:60px;margin:0 auto 14px}
.foot-brand .brand-name{font-size:42px}
.foot-brand .brand-tag{font-size:18px;margin-top:4px}
.foot-h{font-family:"Righteous",sans-serif;font-size:22px;color:var(--white)}
.foot-links{font-size:14px;color:var(--white);line-height:26px}
.news-input{left:766px;top:3563px;width:262px;height:40px;border-radius:20px;background:var(--white);font-size:14px;color:var(--ink);padding:11px 14px}
.btn-sub{left:766px;top:3619px;width:89px;height:36px;line-height:36px;background:var(--orange);font-size:13px}
.foot-line{left:172px;top:3730px;width:856px;height:1px;background:#888}
.copy{left:0;top:3768px;width:1200px;text-align:center;font-family:"Righteous",sans-serif;font-size:14px;color:var(--white)}
</style>
</head>
<body>

<div class="abs notice"><strong>Post-Covid</strong> sourcing and producing management: introducing our competence on managing sourcing and overseas production under the travel restriction and the growing tension on global trading.</div>
<div class="abs notice-close">×</div>

<header class="abs nav"></header>
<div class="abs brand">
  <span class="brand-dot"></span>
  <div><div class="brand-name">CargoBloom</div><div class="brand-tag">Global sourcing and trading</div></div>
</div>
<nav class="abs menu"><span class="active">Home</span><span>About Us</span><span>Services</span><span>Categories</span><span>Form</span><span>Contact</span></nav>

<section class="abs hero">
  <div class="hero-photo" role="img" aria-label="Container ship loaded with colourful containers leaving a harbour"></div>
</section>
<h1 class="abs hero-title">CargoBloom</h1>
<p class="abs hero-sub">Let us handle the overseas sourcing<br>and production for you.</p>
<svg class="abs hero-wave" width="1200" height="110" viewBox="0 0 1200 110">
  <path d="M0 40 C120 50 200 80 320 60 C450 35 560 40 700 55 C850 70 950 20 1060 25 C1130 28 1170 40 1200 45 V110 H0Z" fill="var(--teal)"/>
  <path d="M0 60 C150 70 260 95 420 62 C560 35 650 58 780 65 C900 70 980 30 1090 35 C1150 38 1180 48 1200 52 V110 H0Z" fill="var(--orange)"/>
  <path d="M0 70 C160 110 300 110 450 85 C600 60 700 80 850 85 C1000 90 1100 60 1200 70 V110 H0Z" fill="var(--white)"/>
</svg>

<div class="abs sec-head about-head"><span class="sec-mark"></span><span><span class="hl">ABOUT</span> US</span></div>
<p class="abs about-text">We are a professional team with mature global sourcing and trading experience. We have branch office in Hong Kong and local resources around all areas in China , India and other Asian countries.</p>
<a class="abs btn btn-more">READ MORE</a>
<div class="abs about-visual" role="img" aria-label="Large brand globe decoration"></div>

<svg class="abs flow-bg" width="1200" height="960" viewBox="0 0 1200 960">
  <path d="M0 60 C150 0 300 -10 450 30 C600 70 700 80 850 50 C1000 20 1100 0 1200 30 V900 C1100 880 1000 950 850 930 C700 910 600 860 450 880 C300 900 150 960 0 930Z" fill="var(--grey-bg)"/>
</svg>
<div class="abs sec-head flow-head"><span class="sec-mark"></span><span><span class="hl">OUR WORKING</span> FLOW</span></div>

<!-- row 1 -->
<div class="abs step" style="left:223px;top:1424px">
  <svg width="52" height="52" viewBox="0 0 52 52" fill="none" stroke="var(--teal)" stroke-width="2.5"><rect x="8" y="4" width="30" height="42" rx="2"/><path d="M14 16h18M14 24h18M14 32h10"/><path d="M44 22 30 40l-4 2 1-5 14-17z" stroke="var(--orange)"/></svg>
  <div class="lbl">Received Inquiry</div></div>
<div class="abs step" style="left:508px;top:1424px">
  <svg width="52" height="52" viewBox="0 0 52 52" fill="none" stroke="var(--orange)" stroke-width="2.5"><path d="M26 4c8 8 10 18 6 30H20C16 22 18 12 26 4z"/><circle cx="26" cy="18" r="3"/><path d="M20 28l-6 8h7M32 28l6 8h-7M24 40v6M28 40v6"/></svg>
  <div class="lbl">Start Sourcing</div></div>
<div class="abs step" style="left:793px;top:1424px">
  <svg width="52" height="52" viewBox="0 0 52 52" fill="none" stroke="var(--teal)" stroke-width="2.5"><rect x="4" y="8" width="36" height="32" rx="3"/><path d="M4 16h36M12 4v8M32 4v8"/><circle cx="38" cy="36" r="10" fill="#fff"/><path d="M38 30v6l4 3"/></svg>
  <div class="lbl" style="font-size:15px">Give price and delivery date</div></div>
<!-- row 2 -->
<div class="abs step" style="left:223px;top:1638px">
  <svg width="52" height="52" viewBox="0 0 52 52" fill="none" stroke="var(--orange)" stroke-width="2.5"><circle cx="26" cy="12" r="9"/><path d="M26 7v10M23 9h5a2 2 0 010 4h-4a2 2 0 000 4h5"/><path d="M4 32l10-6 8 4 8-4 8 4 10-2M12 40l8 6 10-4 10-8"/></svg>
  <div class="lbl" style="font-size:17px">kick- off production</div></div>
<div class="abs step" style="left:508px;top:1638px">
  <svg width="60" height="52" viewBox="0 0 60 52" fill="none" stroke="var(--teal)" stroke-width="2.5"><rect x="4" y="10" width="34" height="26" rx="2"/><path d="M38 18h10l8 9v9H38z"/><circle cx="14" cy="40" r="5" fill="#fff"/><circle cx="46" cy="40" r="5" fill="#fff"/></svg>
  <div class="lbl" style="font-size:15px">Deliver Pre-production sample</div></div>
<div class="abs step" style="left:793px;top:1638px">
  <svg width="60" height="52" viewBox="0 0 60 52" fill="none" stroke="var(--orange)" stroke-width="2.5"><path d="M6 44h48L40 10 6 44z"/><path d="M16 34l18-18M22 40l18-18"/></svg>
  <div class="lbl" style="font-size:15px">Arrange samples for clients</div></div>
<!-- row 3 -->
<div class="abs step" style="left:223px;top:1849px">
  <svg width="52" height="52" viewBox="0 0 52 52" fill="none" stroke="var(--teal)" stroke-width="2.5"><rect x="4" y="4" width="32" height="36"/><path d="M14 4v10l6-3 6 3V4"/><circle cx="34" cy="34" r="7" fill="#fff" stroke="var(--orange)"/><path d="M39 39l8 8" stroke="var(--orange)"/></svg>
  <div class="lbl" style="font-size:14px">Arrange inspection through the whole production</div></div>
<div class="abs step" style="left:508px;top:1849px">
  <svg width="52" height="52" viewBox="0 0 52 52" fill="none" stroke="var(--orange)" stroke-width="2.5"><path d="M6 14l26-8 14 6v28l-26 8-14-6z"/><path d="M6 14l14 6 26-8M20 20v28"/><path d="M12 28v6M10 30l2-2 2 2"/></svg>
  <div class="lbl" style="font-size:15px">Arrange shipment to client</div></div>
<div class="abs flow-end" role="img" aria-label="Brand globe decoration"></div>

<!-- flow arrows -->
<svg class="abs" style="left:0;top:1420px" width="1200" height="600" viewBox="0 0 1200 600" fill="none" stroke="var(--orange)" stroke-width="5" stroke-linecap="round">
  <g id="hr"><path d="M428 66c10 12 30 14 66 14"/><path d="M428 78c10 10 30 12 66 12"/><path d="M488 72l10 12-10 6"/></g>
  <use href="#hr" x="285"/>
  <path d="M1012 120c12 20 14 60 12 156M1024 116c18 22 22 70 20 174"/><path d="M1014 270l10 14 10-14"/>
  <path d="M494 266c-10 12-30 14-66 14M494 278c-10 10-30 12-66 12"/><path d="M434 272l-10 12 10 6"/>
  <path d="M779 266c-10 12-30 14-66 14M779 278c-10 10-30 12-66 12"/><path d="M719 272l-10 12 10 6"/>
  <path d="M194 316c-14 20-18 70-16 160M178 314c-20 26-24 70-22 166"/><path d="M132 474l10 14 10-14"/>
  <use href="#hr" y="425"/>
  <use href="#hr" x="285" y="425"/>
</svg>

<svg class="abs cat-bg" width="1200" height="740" viewBox="0 0 1200 740">
  <defs><linearGradient id="sky" x1="0" y1="0" x2="0" y2="1"><stop offset="0" stop-color="#fff"/><stop offset=".25" stop-color="#d8c8d2"/><stop offset=".5" stop-color="#c59a9a"/><stop offset=".75" stop-color="#6f6f84"/><stop offset="1" stop-color="#4d5a70"/></linearGradient></defs>
  <path d="M0 0H1200V740H0Z" fill="url(#sky)" role="img" aria-label="City harbour at dusk seen from above"/>
  <path d="M0 0H1200V60C1050 20 950 70 800 60C650 50 500 -10 300 10C180 22 80 30 0 40Z" fill="var(--grey-bg)"/>
  <path d="M0 690C150 620 300 600 500 650C700 700 850 600 1000 630C1100 650 1160 660 1200 640V740H0Z" fill="var(--white)"/>
</svg>
<div class="abs sec-head cat-head"><span class="sec-mark"></span><span><span class="hl">OUR PRODUCT</span> CATEGORIES</span></div>

<div class="abs cat" style="left:138px;top:2372px"><div class="cat-fill" role="img" aria-label="Clothing on hangers" style="background:linear-gradient(135deg,#e9d8cc,#9c7a6a)"></div><div class="cat-label" style="background:var(--orange);border-radius:50% 50% 0 0/60% 60% 0 0">CLOTHING</div></div>
<div class="abs cat" style="left:373px;top:2372px"><div class="cat-fill" role="img" aria-label="Rows of leather shoes" style="background:linear-gradient(135deg,#5a4a40,#1f1b18)"></div><div class="cat-label" style="background:var(--teal);border-radius:50% 50% 0 0/60% 60% 0 0">SHOES</div></div>
<div class="abs cat" style="left:605px;top:2372px"><div class="cat-fill" role="img" aria-label="Leather bag in an airport hall" style="background:linear-gradient(135deg,#c7ccd2,#a86a3a)"></div><div class="cat-label" style="background:var(--orange);border-radius:50% 50% 0 0/60% 60% 0 0">BAGS</div></div>
<div class="abs cat" style="left:839px;top:2372px"><div class="cat-fill" role="img" aria-label="Wristwatch and accessories" style="background:linear-gradient(135deg,#6a5a52,#2a2523)"></div><div class="cat-label" style="background:var(--teal);border-radius:50% 50% 0 0/60% 60% 0 0">ACCESSORIES</div></div>
<svg class="abs chev" style="left:52px" width="34" height="58" viewBox="0 0 34 58" fill="none" stroke="#fff" stroke-width="3"><path d="M30 2 4 29l26 27"/></svg>
<svg class="abs chev" style="left:1110px" width="34" height="58" viewBox="0 0 34 58" fill="none" stroke="#fff" stroke-width="3"><path d="M4 2l26 27L4 56"/></svg>

<div class="abs enq-bg" role="img" aria-label="Faded container ship at sea"></div>
<div class="abs sec-head enq-head"><span class="sec-mark"></span><span><span class="hl">START AN</span> ENQUIRY</span></div>
<div class="abs field" style="left:172px;top:2985px;width:208px">Name</div>
<div class="abs field" style="left:388px;top:2985px;width:209px">Company Name</div>
<div class="abs field" style="left:603px;top:2985px;width:209px">Email</div>
<div class="abs field" style="left:818px;top:2985px;width:210px">Phone Number</div>
<div class="abs field msg">Message</div>
<a class="abs btn btn-submit">SUBMIT HERE</a>

<svg class="abs foot-wave" width="1200" height="80" viewBox="0 0 1200 80">
  <path d="M0 30C150 60 300 60 450 30C600 0 750 10 900 30C1030 48 1120 40 1200 20V80H0Z" fill="var(--orange)"/>
  <path d="M0 45C200 30 320 -5 500 20C680 45 800 50 950 35C1080 22 1150 25 1200 35V80H0Z" fill="var(--teal)"/>
  <path d="M0 75C40 60 120 50 300 55C480 60 650 45 800 48C950 52 1100 65 1200 55V80H0Z" fill="var(--dark)"/>
</svg>
<footer class="abs footer"></footer>
<div class="abs foot-brand"><span class="brand-dot" style="display:block"></span><div class="brand-name">CargoBloom</div><div class="brand-tag">Global sourcing and trading</div></div>
<div class="abs foot-h" style="left:526px;top:3520px">QUICK LINKS</div>
<div class="abs foot-links" style="left:526px;top:3566px">Home<br>About Us<br>Services<br>Categories</div>
<div class="abs foot-links" style="left:646px;top:3566px">Form<br>Contact</div>
<div class="abs foot-h" style="left:766px;top:3520px">NEWSLETTER SIGNUP</div>
<div class="abs news-input">Email</div>
<a class="abs btn btn-sub">SUBSCRIBE</a>
<div class="abs foot-line"></div>
<div class="abs copy">COPYRIGHTS @ 2020 CARGO BLOOM | ALL RIGHTS RESERVED</div>

</body>
</html>
```